Professional and creative business card design for recruiting service providers

Our company supports German medium-sized companies in filling vacancies promptly. For this we use social media marketing and bring our customers into the visibility.

We want a professional but also creative design for our business cards.

Please look at lindqvar-staff.de to get an impression of our CI.

Target Market(s)

Small and medium-sized companies in Germany from the industry

Industry/Entity Type

Industrie, Handwerk

Contact Information for Business Card

Name, Position, Telefonnummer, Email, Website

Colors
EE7325
F08F49
F5BC92
FAE3D3
FDF4ED

Requirements
Must have
• A picture of the employee and in the style of www.lindqvar-staff.de

```html
<!DOCTYPE html>
<html lang="de">
<head>
<meta charset="UTF-8">
<title>Lindqvar &amp; Staff – Visitenkarte</title>
<link href="https://fonts.googleapis.com/css2?family=Montserrat:wght@400;600;700;800&family=Arimo:wght@400&display=swap" rel="stylesheet">
<style>
  :root {
    --orange: #ee7325;
    --orange-deep: #e8571f;
    --ink: #1a1a1a;
    --card-dark: #2b2b2b;
    --emboss: #3a3a3a;
    --photo-light: #e4e2e4;
    --photo-dark: #4a4a52;
    --stage: #c9c9c9;
    --white: #ffffff;
  }
  * { box-sizing: border-box; margin: 0; padding: 0; }
  html, body {
    width: 1200px; height: 800px; overflow: hidden;
    background: var(--stage);
  }
  .stage {
    width: 1200px; height: 800px;
    display: flex; align-items: center; justify-content: center; gap: 40px;
  }
  .card {
    width: 560px; height: 320px; position: relative;
    border-bottom: 4px solid var(--orange-deep);
    box-shadow: 0 12px 28px rgba(0,0,0,.25);
  }
  /* Front */
  .card--front { background: var(--white); }
  .brand {
    position: absolute; left: 36px; top: 60px;
    display: flex; align-items: center; gap: 14px;
  }
  .brand__mark { width: 36px; height: 36px; background: var(--orange); }
  .brand__name {
    font-family: "Montserrat", sans-serif; font-weight: 800;
    font-size: 21px; line-height: 1.05; letter-spacing: 1.5px;
    color: var(--ink); text-transform: uppercase;
  }
  .person { position: absolute; left: 36px; top: 140px; }
  .person__name {
    font-family: "Montserrat", sans-serif; font-weight: 800;
    font-size: 22px; letter-spacing: 1px; color: var(--orange);
    text-transform: uppercase;
  }
  .person__role {
    font-family: "Arimo", sans-serif; font-size: 14px; color: var(--ink);
    margin-top: 2px;
  }
  .contact { list-style: none; margin-top: 16px; }
  .contact__item {
    display: flex; align-items: center; gap: 10px;
    font-family: "Arimo", sans-serif; font-size: 14px; color: var(--ink);
    line-height: 22px;
  }
  .contact__icon { width: 14px; height: 14px; flex: none; }
  .contact__accent { color: var(--orange); }
  .photo {
    position: absolute; right: 36px; top: 36px;
    width: 226px; height: 226px;
    border: 2px solid var(--orange-deep);
    background: linear-gradient(160deg, var(--photo-light) 55%, var(--photo-dark) 100%);
  }
  /* Back */
  .card--back {
    background: var(--card-dark);
    display: flex; align-items: center; justify-content: center; gap: 18px;
  }
  .back__mark { width: 70px; height: 70px; background: var(--emboss); }
  .back__name {
    font-family: "Montserrat", sans-serif; font-weight: 800;
    font-size: 34px; line-height: 1.05; letter-spacing: 3px;
    color: var(--emboss); text-transform: uppercase;
  }
</style>
</head>
<body>
<main class="stage">
  <section class="card card--front">
    <div class="brand">
      <span class="brand__mark"></span>
      <p class="brand__name">Lindqvar<br>&amp; Staff</p>
    </div>
    <div class="person">
      <h1 class="person__name">Mattis Brenner</h1>
      <p class="person__role">Managing Director</p>
      <ul class="contact">
        <li class="contact__item">
          <svg class="contact__icon" viewBox="0 0 24 24"><path fill="#ee7325" d="M6.6 10.8a15.1 15.1 0 0 0 6.6 6.6l2.2-2.2c.3-.3.7-.4 1-.2 1.1.4 2.3.6 3.6.6.6 0 1 .4 1 1V20c0 .6-.4 1-1 1A17 17 0 0 1 3 4c0-.6.4-1 1-1h3.5c.6 0 1 .4 1 1 0 1.3.2 2.5.6 3.6.1.3 0 .7-.2 1z"/></svg>
          044-987 654 321
        </li>
        <li class="contact__item">
          <svg class="contact__icon" viewBox="0 0 24 24"><path fill="#ee7325" d="M2 5h20v14H2z"/><path fill="none" stroke="#fff" stroke-width="2" d="M2 5l10 8 10-8"/></svg>
          info@lindqvar-staff.de
        </li>
        <li class="contact__item">
          <svg class="contact__icon" viewBox="0 0 24 24"><circle cx="12" cy="12" r="10" fill="none" stroke="#ee7325" stroke-width="2.2"/><path fill="none" stroke="#ee7325" stroke-width="2" d="M2 12h20M12 2c3 3 3 17 0 20M12 2c-3 3-3 17 0 20"/></svg>
          <span>www.<span class="contact__accent">lindqvar-staff</span>.de</span>
        </li>
      </ul>
    </div>
    <div class="photo" role="img" aria-label="Portraitfoto des Mitarbeiters in dunklem Sakko vor hellgrauem Hintergrund"></div>
  </section>

  <section class="card card--back">
    <span class="back__mark"></span>
    <p class="back__name">Lindqvar<br>&amp; Staff</p>
  </section>
</main>
</body>
</html>
```